Business card for Luxury Portable Restroom Trailer company

We are a Luxury Portable Restroom Trailer Company Called FALCRIDGE HIRES. Based in Orange County California. We provide portable restroom trailers for events, such as, Weddings, Concerts, Charity events, Sporting events, Tournaments, Corporate events, ect. We rent and Sell the Luxury restrooms. Our colors are white, grey, and Orange. As you will see in the logo we uploaded.
There are 2 people in the company so the names and titles will change for the 3 people but card will remain the same. Here is the information for each Person: Dwight Penner CFO 555 318-0476
next Person: Leon Marchetti VP 555 318-0476
Next Person: Owen Marchetti CEO 555 318-0476
Information to include on the card: Luxury Restroom Trailers Rental and Sales. Weddings, Concerts, Charity, Sporting and Corp. Events.

```html
<!DOCTYPE html>
<html lang="en">
<head>
<meta charset="utf-8">
<title>Falcridge Hires – Business Card</title>
<link rel="stylesheet" href="https://fonts.googleapis.com/css2?family=Montserrat:wght@400;500;700;800&display=swap">
<style>
  :root {
    --orange: #f26b24;
    --grey: #58595b;
    --ink: #1c1c1c;
    --white: #ffffff;
    --backdrop: #a3a6a7;
  }
  * { margin: 0; padding: 0; box-sizing: border-box; }
  html, body {
    width: 1179px; height: 1200px; overflow: hidden;
    background: var(--backdrop);
    font-family: "Montserrat", Arial, sans-serif;
  }
  .card {
    position: absolute;
    left: 221px;
    width: 738px;
    height: 423px;
    overflow: hidden;
  }
  .card-front { top: 162px; background: var(--white); }
  .card-back { top: 619px; background: var(--orange); }

  .brand-name {
    position: absolute;
    left: 36px; top: 60px;
    font-weight: 800;
    font-size: 30px;
    letter-spacing: 1px;
    color: var(--grey);
  }

  .band {
    position: absolute;
    left: 0; top: 189px;
    width: 100%; height: 94px;
    background: var(--orange);
  }
  .emblem {
    position: absolute;
    left: 532px; top: 163px;
    width: 144px; height: 144px;
  }

  .contact { position: absolute; line-height: 1; }
  .contact .name {
    font-weight: 700; font-size: 24px; letter-spacing: 0.2px;
    color: var(--orange);
  }
  .contact .title {
    font-weight: 400; font-size: 18px; margin-top: 10px;
    color: var(--ink);
  }
  .contact .phone {
    display: flex; align-items: center; gap: 8px;
    font-weight: 500; font-size: 18px; margin-top: 10px;
    color: var(--ink);
  }
  .phone-icon { width: 18px; height: 14px; fill: var(--orange); }

  .contact-cfo { right: 49px; top: 53px; text-align: right; }
  .contact-cfo .phone { justify-content: flex-end; }
  .contact-cfo .phone .phone-icon { order: 2; }

  .contact-vp { left: 35px; top: 198px; }
  .contact-vp .name, .contact-vp .title, .contact-vp .phone { color: var(--white); }
  .contact-vp .phone-icon { fill: var(--white); }

  .contact-ceo { left: 35px; top: 306px; }

  .back-brand {
    position: absolute;
    left: 0; right: 0; top: 140px;
    text-align: center;
    font-weight: 800;
    font-size: 54px;
    letter-spacing: 2px;
    color: var(--white);
  }
  .services {
    position: absolute;
    left: 0; right: 0; top: 320px;
    text-align: center;
    color: var(--white);
    font-size: 18px;
    font-weight: 400;
    line-height: 27px;
  }
  .services li { display: inline; list-style: none; }
  .services li::before {
    content: "";
    display: inline-block;
    width: 11px; height: 11px;
    border-radius: 50%;
    background: var(--white);
    margin: 0 8px 1px 10px;
    vertical-align: middle;
  }
</style>
</head>
<body>
  <svg width="0" height="0" style="position:absolute">
    <symbol id="phone" viewBox="0 0 18 14">
      <path d="M1 4.5C1 2.5 4.5 1 9 1s8 1.5 8 3.5v1.2h-4V4.2c-1-.4-2.5-.6-4-.6s-3 .2-4 .6v1.5H1z"/>
      <path d="M4.2 6.5 6 4.6h6l1.8 1.9L15 13H3z"/>
    </symbol>
  </svg>

  <section class="card card-front">
    <div class="brand-name">FALCRIDGE HIRES</div>

    <div class="contact contact-cfo">
      <div class="name">DWIGHT PENNER</div>
      <div class="title">CFO</div>
      <div class="phone"><svg class="phone-icon"><use href="#phone"/></svg><span>555 318-0476</span></div>
    </div>

    <div class="band"></div>
    <svg class="emblem" viewBox="0 0 144 144" aria-hidden="true">
      <circle cx="72" cy="72" r="72" fill="#ffffff"/>
      <circle cx="72" cy="72" r="60" fill="#f26b24"/>
      <circle cx="72" cy="72" r="53" fill="none" stroke="#ffffff" stroke-width="3"/>
    </svg>

    <div class="contact contact-vp">
      <div class="name">LEON MARCHETTI</div>
      <div class="title">VP</div>
      <div class="phone"><svg class="phone-icon"><use href="#phone"/></svg><span>555 318-0476</span></div>
    </div>

    <div class="contact contact-ceo">
      <div class="name">OWEN MARCHETTI</div>
      <div class="title">CEO</div>
      <div class="phone"><svg class="phone-icon"><use href="#phone"/></svg><span>555 318-0476</span></div>
    </div>
  </section>

  <section class="card card-back">
    <div class="back-brand">FALCRIDGE HIRES</div>
    <ul class="services">
      <li>Luxury Restroom Trailers Rental and Sales</li><br>
      <li>Weddings</li>
      <li>Concerts</li>
      <li>Charity</li>
      <li>Sporting and Corp</li>
      <li>Events</li>
    </ul>
  </section>
</body>
</html>
```